KVOR Individual and Corporate Development Business Card Design

KVOR needs a business card design that is aligned with it's values and targetted markets. Coherent Lattice of Adaptive Reasoning Method's self diagnosis model and tools, which can be used for personal improvement and team/business performance enhancement, is based on the learnings of over 20 years of medical practitioning. KVOR supercharges personal effectiveness and awareness to also increase team and business performance.

The targetted markets are high performance individuals and teams who aspire seek to enhance their capabilities and achieve their absolute best potential.

Look and feel for the business card design we are looking for is high technology, premium, fresh, new and medical.

Target Market(s)

Industry/Entity Type

Business Consultant

Contact Information for Business Card

Logo, Full Name, Title, Phone number, Email, company name, Address,

Font styles to use
Sans Serif

Requirements
Must have
• Tag line: Elevating Potential for Driven Teams and Leaders
• Please use same colours as the logo.

```html
<!DOCTYPE html>
<html lang="en">
<head>
<meta charset="utf-8">
<title>KVOR Business Card</title>
<link rel="stylesheet" href="https://fonts.googleapis.com/css2?family=Roboto:ital,wght@0,400;0,500;0,700;1,400&family=Roboto+Condensed:wght@500;700&display=swap">
<style>
  :root {
    --backdrop: #2b2b2b;
    --teal: #04a8bf;
    --teal-soft: #cfe9ee;
    --paper: #f1f1f1;
    --ink: #555a5c;
    --ink-strong: #4a4f51;
    --white: #ffffff;
  }
  * { margin: 0; padding: 0; box-sizing: border-box; }
  html, body {
    width: 1200px; height: 960px; overflow: hidden;
    background: var(--backdrop);
    font-family: "Roboto", Arial, sans-serif;
  }
  .stage { position: relative; width: 1200px; height: 960px; }
  .card {
    position: absolute; width: 600px; height: 343px; overflow: hidden;
  }
  .card--front { left: 314px; top: 113px; background: var(--paper); }
  .card--back { left: 311px; top: 472px; background: var(--teal); }

  .brand { position: absolute; font-weight: 700; line-height: 1; }
  .brand__name { font-size: 54px; letter-spacing: 2px; }
  .brand__full { font-size: 13px; letter-spacing: 0.6px; text-transform: uppercase; line-height: 15px; margin-top: 8px; }
  .card--front .brand { left: 31px; top: 58px; color: var(--teal); }
  .card--back .brand { left: 0; right: 0; top: 138px; text-align: center; color: var(--white); }
  .card--back .brand__name { font-size: 62px; }
  .card--back .brand__full { font-size: 15px; line-height: 17px; margin-top: 10px; }

  .brand-field {
    position: absolute; right: 0; top: 0; width: 330px; height: 343px;
    background: linear-gradient(100deg, rgba(241,241,241,0) 10%, #e2e2e2 45%, var(--teal-soft) 75%, #dcdcdc 100%);
  }

  .contact { position: absolute; left: 31px; top: 173px; color: var(--ink); font-size: 14px; line-height: 18px; }
  .contact__company { font-weight: 500; color: var(--ink-strong); width: 200px; }
  .contact__address { margin-top: 5px; }
  .contact__lines { list-style: none; margin-top: 8px; }
  .contact__lines li { display: flex; align-items: center; gap: 8px; height: 19px; }
  .contact__lines svg { width: 13px; height: 13px; fill: var(--teal); flex: none; }

  .person { position: absolute; right: 37px; top: 213px; text-align: right; }
  .person__name { font-family: "Roboto Condensed", Arial, sans-serif; font-weight: 700; font-size: 21px; color: var(--teal); }
  .person__title { font-family: "Roboto Condensed", Arial, sans-serif; font-weight: 700; font-size: 15px; color: var(--ink-strong); margin-top: 3px; }

  .tagline { position: absolute; left: 0; right: 0; top: 292px; text-align: center; color: var(--white); font-style: italic; font-size: 14px; }
</style>
</head>
<body>
<main class="stage">
  <section class="card card--front">
    <div class="brand-field" role="img" aria-label="Brand decoration area"></div>
    <div class="brand">
      <div class="brand__name">KVOR</div>
      <div class="brand__full">Coherent Lattice of<br>Adaptive Reasoning Method</div>
    </div>
    <div class="contact">
      <p class="contact__company">Coherent Lattice of Adaptive Reasoning Method</p>
      <p class="contact__address">4120 Harborview Court<br>Juneau, Alaska 99801</p>
      <ul class="contact__lines">
        <li><svg viewBox="0 0 24 24"><path d="M6.6 10.8a15.1 15.1 0 0 0 6.6 6.6l2.2-2.2c.3-.3.7-.4 1-.2 1.1.4 2.3.6 3.6.6.6 0 1 .4 1 1V20c0 .6-.4 1-1 1C10.6 21 3 13.4 3 4c0-.6.4-1 1-1h3.5c.6 0 1 .4 1 1 0 1.3.2 2.5.6 3.6.1.3 0 .7-.2 1z"/></svg>907 555 0148</li>
        <li><svg viewBox="0 0 24 24"><path d="M2 5h20v14H2zm2 2v.5l8 5 8-5V7l-8 5z"/></svg>hello@kvormethod.com</li>
        <li><svg viewBox="0 0 24 24"><circle cx="12" cy="12" r="10"/></svg>www.kvormethod.com</li>
      </ul>
    </div>
    <div class="person">
      <p class="person__name">DANIEL REYES</p>
      <p class="person__title">CEO/FOUNDER</p>
    </div>
  </section>

  <section class="card card--back">
    <div class="brand">
      <div class="brand__name">KVOR</div>
      <div class="brand__full">Coherent Lattice of<br>Adaptive Reasoning Method</div>
    </div>
    <p class="tagline">Elevating Potential for Driven Teams and Leaders</p>
  </section>
</main>
</body>
</html>
```